Modern Business Card

Modern professional business card with more than just logo and demographic info. Something memorable.

We are a trendy/modern chiropractic group with an emphasis on neurology, hence the minimalist-type brain logo. We want to convey that modern and technical aspect with professionalism and the elite nature of our practice environment.

```html
<!DOCTYPE html>
<html lang="en">
<head>
<meta charset="utf-8">
<title>Keystone Spine – Business Card</title>
<link href="https://fonts.googleapis.com/css2?family=Quattrocento:wght@400&family=Khand:wght@500&family=Roboto:wght@400&display=swap" rel="stylesheet">
<style>
  :root {
    --backdrop: #b7b7b7;
    --card: #f1f1f0;
    --brand-blue: #3d5f9b;
    --brand-dark: #3a2f31;
    --ink: #111111;
    --on-blue: #ffffff;
    --on-blue-soft: #e4e9f3;
  }
  * { box-sizing: border-box; margin: 0; padding: 0; }
  html, body {
    width: 1200px; height: 576px; overflow: hidden;
    background: var(--backdrop);
  }
  .canvas { position: relative; width: 1200px; height: 576px; }

  .card {
    position: absolute; top: 138px;
    width: 484px; height: 292px;
    background: var(--card);
    border-radius: 10px; overflow: hidden;
  }
  .card--front { left: 82px; }
  .card--back { left: 602px; }

  /* Brand name lockup */
  .brand {
    position: absolute; display: flex; align-items: center;
    font-family: "Quattrocento", serif; font-weight: 400;
    color: var(--brand-dark); text-transform: uppercase;
  }
  .brand__square { background: var(--brand-blue); flex: none; }
  .brand__name { line-height: 0.95; letter-spacing: 0.02em; }

  .card--front .brand { left: 78px; top: 86px; gap: 16px; }
  .card--front .brand__square { width: 62px; height: 62px; }
  .card--front .brand__name { font-size: 40px; }

  .card--back .brand { left: 26px; top: 118px; gap: 10px; }
  .card--back .brand__square { width: 40px; height: 40px; }
  .card--back .brand__name { font-size: 24px; }

  /* Front */
  .front__web {
    position: absolute; left: 0; right: 0; top: 245px;
    display: flex; justify-content: center; align-items: center; gap: 22px;
    font-family: "Roboto", sans-serif; font-size: 12.5px; color: var(--ink);
  }
  .front__dash { width: 34px; height: 4px; }
  .front__band { position: absolute; left: 0; right: 0; bottom: 0; height: 11px; display: flex; }
  .front__band-blue { flex: 1; background: var(--brand-blue); }
  .front__band-dark { flex: 1; background: var(--brand-dark); }

  /* Back */
  .back__panel { position: absolute; inset: 0; }
  .back__details { position: absolute; left: 278px; top: 66px; color: var(--on-blue); }
  .back__name { font-family: "Khand", sans-serif; font-weight: 500; font-size: 21px; line-height: 1.1; }
  .back__role { font-family: "Quattrocento", serif; font-size: 12px; color: var(--on-blue-soft); margin-top: 3px; }
  .contact { list-style: none; margin-top: 22px; font-family: "Quattrocento", serif; font-size: 12px; color: var(--on-blue-soft); }
  .contact li { display: flex; align-items: center; gap: 9px; height: 18.5px; }
  .contact svg { width: 11px; height: 11px; flex: none; }
  .back__address { font-family: "Quattrocento", serif; font-size: 12px; line-height: 18px; color: var(--on-blue-soft); margin-top: 4px; }
</style>
</head>
<body>
<main class="canvas">

  <section class="card card--front" aria-label="Card front">
    <div class="brand">
      <span class="brand__square"></span>
      <span class="brand__name">Keystone<br>Spine</span>
    </div>
    <div class="front__web">
      <svg class="front__dash" viewBox="0 0 34 4"><path d="M0 2 L34 0 L34 4 Z" fill="var(--brand-blue)"/></svg>
      <span>www.keystonespine.com</span>
      <svg class="front__dash" viewBox="0 0 34 4"><path d="M0 0 L34 2 L0 4 Z" fill="var(--brand-blue)"/></svg>
    </div>
    <div class="front__band">
      <span class="front__band-blue"></span>
      <span class="front__band-dark"></span>
    </div>
  </section>

  <section class="card card--back" aria-label="Card back">
    <svg class="back__panel" viewBox="0 0 484 292" preserveAspectRatio="none" aria-hidden="true">
      <path d="M216 0 Q 262 150 226 292 L 484 292 L 484 0 Z" fill="var(--brand-dark)"/>
      <path d="M222 0 Q 268 150 233 292 L 484 292 L 484 0 Z" fill="var(--brand-blue)"/>
    </svg>
    <div class="brand">
      <span class="brand__square"></span>
      <span class="brand__name">Keystone<br>Spine</span>
    </div>
    <div class="back__details">
      <p class="back__name">Marcus Lee Hart</p>
      <p class="back__role">Managing Director</p>
      <ul class="contact">
        <li>
          <svg viewBox="0 0 12 12"><path d="M1 4 Q6 0 11 4 L9.5 5.5 L8 4.5 L4 4.5 L2.5 5.5 Z M3 6 H9 L10 11 H2 Z" fill="currentColor"/></svg>
          555-014-2290
        </li>
        <li>
          <svg viewBox="0 0 12 12"><rect x="0.5" y="2.5" width="11" height="7" fill="none" stroke="currentColor"/><path d="M0.5 2.5 L6 7 L11.5 2.5" fill="none" stroke="currentColor"/></svg>
          marcus@keystonespine.com
        </li>
        <li>
          <svg viewBox="0 0 12 12"><circle cx="6" cy="6" r="5" fill="none" stroke="currentColor"/><ellipse cx="6" cy="6" rx="2" ry="5" fill="none" stroke="currentColor"/><path d="M1 6 H11" stroke="currentColor"/></svg>
          www.keystonespine.com
        </li>
      </ul>
      <p class="back__address">58 Harbor Lane, Fairview,<br>Maple Town, US 204815</p>
    </div>
  </section>

</main>
</body>
</html>
```